RTavenor Business Cards & Letterhead

I have a logo but need a design for some new business cards. We are a Design-Build Firm that specializes in the design and construction of commercial projects.
the cards need to be professional. no cartoon stuff.
i would like to have the cards in AI format so I can update the card as needed. Logo is provided.
Our Address is: 4187 Marlowe Ct. Linden Ridge, Oregon 27614

```html
<!DOCTYPE html>
<html lang="en">
<head>
<meta charset="utf-8">
<title>RTavenor Business Card</title>
<link href="https://fonts.googleapis.com/css2?family=Roboto:ital,wght@0,400;0,700;0,900;1,400;1,700&display=swap" rel="stylesheet">
<style>
  :root {
    --backdrop: #dedede;
    --paper: #f4f4f4;
    --brand-blue: #0d5a9e;
    --edge-blue: #1b6fc4;
    --ink: #1e1e1e;
    --charcoal: #333333;
  }
  * { margin: 0; padding: 0; box-sizing: border-box; }
  html, body { width: 1200px; height: 1200px; overflow: hidden; }
  body {
    background: var(--backdrop);
    font-family: "Roboto", Arial, sans-serif;
    position: relative;
  }
  .card {
    position: absolute;
    width: 580px;
    height: 332px;
    background: var(--paper);
    border-right: 4px solid var(--edge-blue);
    border-bottom: 4px solid var(--edge-blue);
    box-shadow: 0 18px 40px rgba(0,0,0,0.12);
    overflow: hidden;
  }
  .card--front { left: 90px; top: 240px; }
  .card--back { left: 530px; top: 620px; }

  .contact { position: absolute; left: 70px; top: 70px; width: 270px; }
  .contact__name {
    color: var(--brand-blue);
    font-weight: 700;
    font-size: 26px;
    letter-spacing: -0.3px;
  }
  .contact__title { font-size: 13px; color: var(--ink); margin-top: 4px; }
  .contact__address {
    font-style: italic;
    font-size: 14px;
    line-height: 1.35;
    color: var(--ink);
    margin-top: 28px;
  }
  .contact__lines { list-style: none; margin-top: 18px; }
  .contact__lines li {
    display: flex;
    align-items: center;
    gap: 6px;
    font-style: italic;
    font-size: 14.5px;
    color: var(--ink);
    line-height: 1.5;
  }
  .contact__lines svg { width: 12px; height: 12px; fill: var(--brand-blue); flex: none; }

  .front-mark {
    position: absolute;
    right: 48px;
    top: 120px;
  }
  .front-mark__name {
    color: var(--brand-blue);
    font-weight: 900;
    font-size: 40px;
    letter-spacing: -0.5px;
  }

  .back-mark {
    position: absolute;
    left: 0; right: 0;
    top: 128px;
    display: flex;
    justify-content: center;
    align-items: flex-start;
    gap: 6px;
  }
  .back-mark__name {
    font-weight: 900;
    font-size: 48px;
    letter-spacing: 1px;
    color: var(--charcoal);
  }
  .back-mark__reg { font-size: 14px; color: var(--charcoal); margin-top: 2px; }

  .corner-block {
    position: absolute;
    right: 30px;
    bottom: 0;
    width: 110px;
    height: 110px;
    background: var(--brand-blue);
  }
</style>
</head>
<body>
  <section class="card card--front">
    <div class="contact">
      <h1 class="contact__name">Rowan Tavenor</h1>
      <p class="contact__title">CEO</p>
      <p class="contact__address">4187 Marlowe Ct. Linden Ridge,<br>Oregon 27614</p>
      <ul class="contact__lines">
        <li><svg viewBox="0 0 24 24"><path d="M6.6 10.8a15 15 0 0 0 6.6 6.6l2.2-2.2a1 1 0 0 1 1-.25 11.4 11.4 0 0 0 3.6.57 1 1 0 0 1 1 1V20a1 1 0 0 1-1 1A17 17 0 0 1 3 4a1 1 0 0 1 1-1h3.5a1 1 0 0 1 1 1c0 1.25.2 2.45.57 3.57a1 1 0 0 1-.25 1z"/></svg>503.555.0148</li>
        <li><svg viewBox="0 0 24 24"><path d="M7 1h10a2 2 0 0 1 2 2v18a2 2 0 0 1-2 2H7a2 2 0 0 1-2-2V3a2 2 0 0 1 2-2zm0 3v14h10V4z"/></svg>503.555.0193</li>
        <li><svg viewBox="0 0 24 24"><path d="M2 5h20v14H2zm2 2v.5l8 5 8-5V7l-8 5z"/></svg>nadia@rtavenor.com</li>
        <li><svg viewBox="0 0 24 24"><path d="M12 2a10 10 0 1 0 0 20 10 10 0 0 0 0-20zm-1 2.1V11H6.05A8 8 0 0 1 11 4.1zm2 0A8 8 0 0 1 17.95 11H13zM6.05 13H11v6.9A8 8 0 0 1 6.05 13zM13 19.9V13h4.95A8 8 0 0 1 13 19.9z"/></svg>www.rtavenor.com</li>
      </ul>
    </div>
    <div class="front-mark">
      <span class="front-mark__name">RTavenor</span>
    </div>
  </section>

  <section class="card card--back">
    <div class="back-mark">
      <span class="back-mark__name">RTAVENOR</span>
      <span class="back-mark__reg">®</span>
    </div>
    <div class="corner-block"></div>
  </section>
</body>
</html>
```